New Business Card for Web Design/Internet Marketing Company

Looking for a great looking new business card. We are a 10 year old web design, internet marketing and website management company that works mostly with small businesses.

Our new card needs to better match the colors and style of our website, be bold, extremely usable and slightly edgy.

Target Market(s)

Small/Medium businesses that have websites

Industry/Entity Type

Internet

Requirements
Must have
• Front and back design, full color, rounded corners please

Must use the colors/style of our website (JPG provided)

INFO FOR CARDS (as readable as possible please)
Mark Lenner
President/CEO
mark@trelvanmedia.example
Phone: 520-381-7459
Toll Free: 866-381-7459
Address: 4315 W. Calloway Ave. Ste. 140, Tucson, AZ 85792

THINGS I WANT TO PROMOTE (if there is room):
1. Our Website - www.trelvanmedia.example

2. Social Media
Twitter: @trelvanmedia
Facebook: www.facebook.com/trelvanmedia

3. Our Services
Web Design
Internet Marketing
Website Management

```html
<!DOCTYPE html>
<html lang="en">
<head>
<meta charset="utf-8">
<title>Trelvan Media – Business Card</title>
<link rel="stylesheet" href="https://fonts.googleapis.com/css2?family=Open+Sans:wght@400;600;700&display=swap">
<style>
  :root {
    --brand-blue: #1b8fcc;
    --brand-orange: #f0812a;
    --card-white: #ffffff;
    --ink-light: #ffffff;
    --ink-muted: #555555;
    --social-fill: #5aa9d8;
    --backdrop: #e9e6e2;
  }
  * { box-sizing: border-box; margin: 0; padding: 0; }
  html, body {
    width: 1200px; height: 402px; overflow: hidden;
    background: var(--backdrop);
    font-family: "Open Sans", sans-serif;
  }
  .stage { position: relative; width: 1200px; height: 402px; }
  .card {
    position: absolute; top: 57px; height: 292px;
    border-radius: 10px; overflow: hidden;
    box-shadow: 0 2px 6px rgba(0,0,0,0.15);
  }
  .card-front { left: 61px; width: 512px; background: var(--card-white); }
  .card-back { left: 625px; width: 512px; background: var(--brand-blue); color: var(--ink-light); }

  .front-wave { position: absolute; inset: 0; }

  .holder { position: absolute; right: 32px; top: 30px; text-align: right; color: var(--brand-blue); }
  .holder-name { font-size: 17px; font-weight: 700; line-height: 1.15; }
  .holder-title { font-size: 11px; font-weight: 400; }

  .brand-front { position: absolute; left: 20px; top: 140px; }
  .brand-name { font-size: 32px; font-weight: 600; color: var(--brand-orange); letter-spacing: -0.5px; line-height: 1; }
  .brand-tagline { font-size: 11px; color: var(--ink-muted); margin-top: 5px; margin-left: 102px; }

  .contact-list {
    position: absolute; right: 32px; top: 186px; list-style: none;
    color: var(--ink-light); font-size: 11.5px; line-height: 19px; text-align: right;
  }
  .contact-list li { display: flex; justify-content: flex-end; align-items: center; gap: 5px; }
  .contact-icon { width: 9px; height: 9px; fill: var(--ink-light); }
  .address { position: absolute; right: 32px; bottom: 10px; color: var(--ink-light); font-size: 11.5px; }

  .brand-back { position: absolute; left: 24px; top: 124px; display: flex; align-items: center; gap: 9px; }
  .brand-back .dot { width: 13px; height: 13px; border-radius: 50%; background: var(--ink-light); }
  .brand-back .brand-name { color: var(--ink-light); font-size: 27px; }

  .social { position: absolute; left: 268px; top: 40px; list-style: none; font-size: 16px; line-height: 24px; }
  .social li { display: flex; align-items: center; gap: 11px; }
  .social-square { width: 17px; height: 17px; border-radius: 3px; background: var(--social-fill); border: 1px solid rgba(255,255,255,0.5); }
  .services { position: absolute; left: 268px; top: 114px; }
  .services-heading { font-size: 24px; font-weight: 600; margin-bottom: 10px; }
  .services-list { list-style: none; font-size: 21px; line-height: 31px; }
</style>
</head>
<body>
<div class="stage">
  <section class="card card-front">
    <svg class="front-wave" width="512" height="292" viewBox="0 0 512 292" aria-hidden="true">
      <path d="M0,246 C120,292 220,250 300,200 C380,150 445,128 512,130 L512,292 L0,292 Z" fill="var(--brand-blue)"/>
      <path d="M0,240 C120,285 215,232 295,184 C375,136 445,112 512,116" fill="none" stroke="var(--brand-orange)" stroke-width="5"/>
    </svg>

    <div class="holder">
      <p class="holder-name">Mark Lenner</p>
      <p class="holder-title">President/CEO</p>
    </div>

    <div class="brand-front">
      <p class="brand-name">Trelvan Media</p>
      <p class="brand-tagline">Grow your Presence</p>
    </div>

    <ul class="contact-list">
      <li>520-381-7459 <svg class="contact-icon" viewBox="0 0 10 10"><circle cx="5" cy="5" r="4.5"/></svg></li>
      <li>866-381-7459 <svg class="contact-icon" viewBox="0 0 10 10"><circle cx="5" cy="5" r="4.5"/></svg></li>
      <li>mark@trelvanmedia.example <svg class="contact-icon" viewBox="0 0 10 10"><rect x="0.5" y="2" width="9" height="6"/></svg></li>
      <li>www.trelvanmedia.example <svg class="contact-icon" viewBox="0 0 10 10"><circle cx="5" cy="5" r="4.5"/></svg></li>
    </ul>
    <p class="address">4315 W. Calloway Ave. Ste. 140, Tucson, AZ 85792</p>
  </section>

  <section class="card card-back">
    <div class="brand-back">
      <span class="dot"></span>
      <p class="brand-name">Trelvan Media</p>
    </div>

    <ul class="social">
      <li><span class="social-square"></span>@trelvanmedia</li>
      <li><span class="social-square"></span>trelvanmedia</li>
    </ul>

    <div class="services">
      <h2 class="services-heading">Our Services</h2>
      <ul class="services-list">
        <li>Web Design</li>
        <li>Internet Marketing</li>
        <li>Website Management</li>
      </ul>
    </div>
  </section>
</div>
</body>
</html>
```